Government contracting small business needs a web design

Tarvex Summit Inc is a veteran owned small business that delivers a full range of professional services as well as training in information technology, security and defense intelligence solutions.
We need a professional/corporate looking website where potential clients can view what services are offered.
This being a new company, there is not much that can added more than a narrative statement, stock photos and a place where potential customers and employees can make contact.
Open to ideas.
Target Market(s)
US Government
Industry/Entity Type
Small Business
Look and feel
Each slider illustrates characteristics of the customer's brand and the style your logo design should communicate.

```html
<!DOCTYPE html>
<html lang="en">
<head>
<meta charset="utf-8">
<title>Tarvex Summit</title>
<link rel="stylesheet" href="https://fonts.googleapis.com/css2?family=Roboto+Condensed:wght@700&family=PT+Sans:wght@400&display=swap">
<style>
  :root {
    --page-top: #727272;
    --page-bottom: #262626;
    --sheet: #ffffff;
    --ink: #111111;
    --muted: #a8a8a8;
    --footer-ink: #9a9a9a;
    --gold: #d09b2c;
    --gold-light: #f2d38c;
    --gold-rule: #b8862a;
    --pill-top: #f8dd6a;
    --pill-bottom: #e2b12b;
    --search: #c9c9c9;
    --search-edge: #8f8f8f;
    --logo-ink: #3c3c3c;
  }
  * { margin: 0; padding: 0; box-sizing: border-box; }
  html, body { width: 1200px; height: 838px; overflow: hidden; }
  body {
    position: relative;
    background: linear-gradient(to bottom, var(--page-top), var(--page-bottom));
    font-family: "PT Sans", Tahoma, sans-serif;
    color: var(--ink);
  }
  .sheet {
    position: absolute; left: 204px; top: 0; width: 800px; height: 784px;
    background: var(--sheet);
  }
  .brand {
    position: absolute; left: 30px; top: 12px; height: 56px;
    display: flex; align-items: center; gap: 10px;
  }
  .brand-mark {
    width: 52px; height: 52px; border-radius: 50%; background: var(--logo-ink);
  }
  .brand-name {
    font-family: "Roboto Condensed", Arial, sans-serif; font-weight: 700;
    font-size: 38px; color: var(--logo-ink); letter-spacing: 0.5px;
  }
  .main-nav {
    position: absolute; left: 0; top: 93px; width: 800px; height: 24px;
    font-size: 12.5px;
  }
  .main-nav a {
    position: absolute; top: 4px; color: var(--ink); text-decoration: none;
  }
  .main-nav a.is-current {
    top: 1px; left: 9px; width: 49px; height: 21px; padding-top: 3px; text-align: center;
    background: linear-gradient(var(--pill-top), var(--pill-bottom));
    border-radius: 2px;
  }
  .search {
    position: absolute; left: 616px; top: 0; width: 174px; height: 24px;
    background: var(--search); border: 1px solid var(--search-edge); border-radius: 5px;
    font-size: 12px; color: #777; padding: 4px 8px;
  }
  .search svg { position: absolute; right: 7px; top: 4px; }
  .hero {
    position: absolute; left: 0; top: 126px; width: 800px; height: 357px;
    background: radial-gradient(ellipse at 55% 40%, #8a8a8a 0%, #3e3e3e 45%, #121212 100%);
  }
  .hero-arrow {
    position: absolute; top: 166px; width: 23px; height: 24px; background: rgba(90,90,90,0.8);
  }
  .hero-arrow.prev { left: 12px; }
  .hero-arrow.next { left: 764px; }
  .hero-title {
    position: absolute; left: 0; width: 800px; top: 312px; text-align: center;
    font-family: "Roboto Condensed", Arial, sans-serif; font-weight: 700;
    font-size: 25px; color: #fff;
  }
  .news {
    position: absolute; left: 7px; top: 490px; width: 204px; height: 288px;
    background: var(--gold); padding: 4px 8px 0 8px;
  }
  .section-title {
    font-family: "Roboto Condensed", Arial, sans-serif; font-weight: 700; font-size: 25px;
    line-height: 30px;
  }
  .news .section-title { color: var(--gold-light); }
  .news-item {
    width: 174px; font-size: 10.2px; line-height: 12px; margin: 6px 0 0 10px;
    padding-bottom: 12px; border-bottom: 1px solid var(--gold-rule);
  }
  .news-item + .news-item { margin-top: 18px; }
  .news-item:last-child { border-bottom: none; }
  .welcome {
    position: absolute; left: 232px; top: 494px; width: 545px;
  }
  .welcome .section-title { color: var(--muted); margin-bottom: 12px; }
  .welcome p { font-size: 10.3px; line-height: 19.2px; margin-bottom: 19px; }
  .site-footer {
    position: absolute; left: 213px; top: 798px; font-size: 10px; color: var(--footer-ink);
  }
</style>
</head>
<body>
  <div class="sheet">
    <header class="brand">
      <span class="brand-mark"></span>
      <span class="brand-name">Tarvex Summit</span>
    </header>

    <nav class="main-nav">
      <a class="is-current" href="#">Home</a>
      <a href="#" style="left:84px">Innovation</a>
      <a href="#" style="left:175px">What We Do</a>
      <a href="#" style="left:275px">Our Company</a>
      <a href="#" style="left:381px">Investors</a>
      <a href="#" style="left:465px">Newsroom</a>
      <a href="#" style="left:551px">Careers</a>
      <div class="search">Search
        <svg width="14" height="14" viewBox="0 0 14 14"><circle cx="5.5" cy="5.5" r="4" fill="none" stroke="#888" stroke-width="1.6"/><line x1="8.5" y1="8.5" x2="13" y2="13" stroke="#888" stroke-width="2"/></svg>
      </div>
    </nav>

    <section class="hero" role="img" aria-label="Black and white photo of a business hand touching a glowing screen frame">
      <span class="hero-arrow prev"><svg width="23" height="24"><polyline points="14,7 9,12 14,17" fill="none" stroke="#ccc" stroke-width="2"/></svg></span>
      <span class="hero-arrow next"><svg width="23" height="24"><polyline points="9,7 14,12 9,17" fill="none" stroke="#ccc" stroke-width="2"/></svg></span>
      <h2 class="hero-title">Army selects Veltrane for common Infrared counter Measures Solution</h2>
    </section>

    <aside class="news">
      <h2 class="section-title">In the News</h2>
      <p class="news-item">Lorem ipsum dolor sit amet, consectetuer adipiscing elit, sed diam nonummy nibh euismod tincidunt ut laoreet dolore magna aliquam erat volutpat.</p>
      <p class="news-item">Lorem ipsum dolor sit amet, consectetuer adipiscing elit, sed diam nonummy nibh euismod tincidunt ut laoreet dolore magna aliquam erat volutpat.</p>
      <p class="news-item">Lorem ipsum dolor sit amet, consectetuer adipiscing elit, sed diam nonummy nibh euismod tincidunt ut laoreet dolore magna aliquam erat volutpat.</p>
    </aside>

    <main class="welcome">
      <h1 class="section-title">Welcome to Tarvex Summit</h1>
      <p>Lorem ipsum dolor sit amet, consectetuer adipiscing elit, sed diam nonummy nibh euismod tincidunt ut laoreet dolore magna aliquam erat volutpat. Ut wisi enim ad minim veniam, quis nostrud exerci tation ullamcorper suscipit lobortis nisl ut aliquip ex ea commodo consequat. Duis autem vel eum iriure dolor in hendrerit in vulputate velit esse molestie consequat, vel illum dolore eu feugiat nulla facilisis at vero eros et accumsan et iusto odio dignissim qui blandit praesent luptatum zzril delenit augue duis dolore te feugait nulla facilisi.</p>
      <p>Lorem ipsum dolor sit amet, consectetuer adipiscing elit, sed diam nonummy nibh euismod tincidunt ut laoreet dolore magna aliquam erat volutpat. Ut wisi enim ad minim veniam, quis nostrud exerci tation ullamcorper suscipit lobortis nisl ut aliquip ex ea commodo consequat. Duis autem vel eum iriure dolor in hendrerit in vulputate velit esse molestie consequat, vel illum dolore eu feugiat nulla facilisis at vero eros et accumsan et iusto odio dignissim qui blandit praesent luptatum zzril delenit augue duis dolore te feugait nulla facilisi.</p>
    </main>
  </div>

  <footer class="site-footer">2012 © Tarvex Summit. All Rights Received.</footer>
</body>
</html>
```